Business Card design for law firm = Brightvale Australia

We are seeking a new design for our business cards.
We are keeping our logo, which is attached.
We need space for
Name
Title
Address is , which is
Level 7
214 Marlowe Street
Sydney NSW 2047
Phone :
Mobile :
Fax :
Email :
DX :
website www.brightvale-example.com.au

Industry/Entity Type

Law Firm / Banking and Finance

Contact Information for Business Card

We are seeking a new design for our business cards. We are keeping our logo. We need space for Name Title Address is Level 7 214 Marlowe Street Sydney NSW 2047 Phone Mobile Fax Email DX website www.brightvale-example.com.au

Colors
0054AA
0677BA
7BADD7
CADEEF
E8F1F8

Requirements
Must have
• see our website for general feel www.brightvale-example.com.au

```html
<!DOCTYPE html>
<html lang="en">
<head>
<meta charset="utf-8">
<title>Brightvale Australia – Business Card</title>
<link href="https://fonts.googleapis.com/css2?family=Crimson+Text:wght@400&family=Open+Sans:wght@400&display=swap" rel="stylesheet">
<style>
  :root {
    --stage: #1c1c1c;
    --blue-deep: #0077bf;
    --blue-bright: #00a3dd;
    --blue-mid: #0a8fd0;
    --white: #ffffff;
    --ink-light: #e8f1f8;
  }
  * { box-sizing: border-box; margin: 0; padding: 0; }
  html, body {
    width: 1200px; height: 1015px; overflow: hidden;
    background: var(--stage);
    font-family: "Open Sans", Arial, sans-serif;
  }
  .stage {
    width: 1200px; height: 1015px;
    display: flex; flex-direction: column; align-items: center; justify-content: center;
    gap: 55px;
  }
  .card {
    width: 700px; height: 400px; position: relative; overflow: hidden;
    box-shadow: 0 18px 40px rgba(0,0,0,.55);
  }

  /* Company name */
  .company { display: flex; align-items: center; gap: 14px; }
  .company__dot { width: 18px; height: 18px; border-radius: 50%; flex: none; }
  .company__name {
    font-family: "Open Sans", Arial, sans-serif;
    font-weight: 400; font-size: 40px; line-height: 1; letter-spacing: 1px;
  }

  /* Front */
  .card--front {
    background: linear-gradient(180deg, var(--blue-bright) 0%, var(--blue-mid) 60%, var(--blue-deep) 100%);
    display: flex; align-items: center; justify-content: center;
  }
  .card--front .company__dot { background: var(--white); }
  .card--front .company__name { color: var(--white); }

  /* Back */
  .card--back { background: var(--white); }
  .card--back .company {
    position: absolute; top: 0; left: 0; right: 0; height: 212px; justify-content: center;
  }
  .card--back .company__dot { background: var(--blue-bright); }
  .card--back .company__name { color: var(--blue-deep); }

  .contact-band {
    position: absolute; left: 0; right: 0; top: 212px; bottom: 0;
    background: var(--blue-deep);
    border-top: 6px solid var(--blue-bright);
    display: flex; align-items: center; padding: 0 30px;
    color: var(--white);
  }
  .person { width: 300px; text-align: right; padding-right: 22px; }
  .person__name { font-family: "Crimson Text", Georgia, serif; font-size: 32px; line-height: 1.05; }
  .person__role, .person__dx { font-size: 16px; line-height: 1.35; }
  .person__address { font-size: 16px; line-height: 1.35; margin-top: 10px; }
  .divider { width: 1px; align-self: stretch; margin: 26px 0; background: rgba(232,241,248,.55); }
  .details { list-style: none; padding-left: 24px; }
  .details li { display: flex; align-items: center; gap: 10px; font-size: 16px; line-height: 1.55; }
  .details svg { width: 16px; height: 16px; flex: none; }
</style>
</head>
<body>
<main class="stage">

  <section class="card card--front" aria-label="Card front">
    <div class="company">
      <span class="company__dot"></span>
      <span class="company__name">Brightvale</span>
    </div>
  </section>

  <section class="card card--back" aria-label="Card back">
    <div class="company">
      <span class="company__dot"></span>
      <span class="company__name">Brightvale</span>
    </div>

    <div class="contact-band">
      <div class="person">
        <p class="person__name">Daniel Harwood</p>
        <p class="person__role">Managing Director</p>
        <p class="person__dx">DX :987654321</p>
        <p class="person__address">Level 7, 214 Marlowe Street<br>Sydney NSW 2047</p>
      </div>
      <span class="divider"></span>
      <ul class="details">
        <li>
          <svg viewBox="0 0 16 16" aria-label="Phone"><path d="M3 1.5l2.5 0 1 3.5-1.6 1.2a8 8 0 0 0 4.9 4.9L11 9.5l3.5 1v2.5c0 .8-.7 1.5-1.5 1.5C6.9 14.5 1.5 9.1 1.5 3c0-.8.7-1.5 1.5-1.5z" fill="#fff"/></svg>
          044-987 654 321
        </li>
        <li>
          <svg viewBox="0 0 16 16" aria-label="Mobile"><rect x="4" y="1" width="8" height="14" rx="1.5" fill="none" stroke="#fff" stroke-width="1.5"/><circle cx="8" cy="12.5" r=".9" fill="#fff"/></svg>
          044-987 654 322
        </li>
        <li>
          <svg viewBox="0 0 16 16" aria-label="Fax"><rect x="4" y="1.5" width="8" height="4" fill="#fff"/><rect x="1.5" y="6" width="13" height="6" rx="1" fill="#fff"/><rect x="4" y="10" width="8" height="4.5" fill="#fff" stroke="#0077bf" stroke-width="1"/></svg>
          044-987 654 323
        </li>
        <li>
          <svg viewBox="0 0 16 16" aria-label="Email"><rect x="1.5" y="3.5" width="13" height="9" fill="#fff"/><path d="M1.5 3.5L8 9l6.5-5.5" fill="none" stroke="#0077bf" stroke-width="1.2"/></svg>
          info@brightvale-example.com.au
        </li>
        <li>
          <svg viewBox="0 0 16 16" aria-label="Website"><g fill="none" stroke="#fff" stroke-width="1.2"><circle cx="8" cy="8" r="6.5"/><ellipse cx="8" cy="8" rx="3" ry="6.5"/><path d="M1.5 8h13M2.5 4.8h11M2.5 11.2h11"/></g></svg>
          www.brightvale-example.com.au
        </li>
      </ul>
    </div>
  </section>

</main>
</body>
</html>
```